Brindle Water - 500ml

to create a water bottle packaging similar to L'onde Claire design. Bottle should be blue similar to PURE FLOW but change the design/logo to Brindle. Wording should be similar just different design and logo. Thanks.

Colors
0054AA
0677BA
7BADD7
CADEEF
E8F1F8

Requirements
Must have
• Bottle must not be in plastic bottles. They are made in a carton instead - see PURE FLOW for reference.

```html
<!DOCTYPE html>
<html lang="en">
<head>
<meta charset="utf-8">
<title>Brindle Water – 500ml carton</title>
<link rel="stylesheet" href="https://fonts.googleapis.com/css2?family=Oswald:wght@400;500;600&family=Open+Sans:wght@400;600&display=swap">
<style>
  :root {
    --carton-blue: #2aaedf;
    --carton-blue-deep: #1f9fd2;
    --navy: #0054aa;
    --ocean: #0677ba;
    --sky: #7badd7;
    --mist: #cadeef;
    --ice: #e8f1f8;
    --snow: #ffffff;
    --backdrop: #eef2f5;
    --display: "Oswald", sans-serif;
    --body: "Open Sans", sans-serif;
  }
  * { box-sizing: border-box; margin: 0; padding: 0; }
  html, body { width: 1200px; height: 3000px; overflow: hidden; }
  body { background: var(--backdrop); position: relative; font-family: var(--display); color: var(--snow); }

  .panel-row { position: absolute; top: 120px; left: 60px; display: flex; gap: 20px; }
  .panel {
    position: relative; width: 255px; height: 880px; background: var(--carton-blue);
    overflow: hidden; font-size: 10px; text-transform: uppercase;
  }
  .panel-fold { position: absolute; top: 0; left: 0; right: 0; height: 5%; background: var(--carton-blue-deep); border-bottom: 1px solid rgba(255,255,255,.35); }

  .peaks {
    position: absolute; left: 0; right: 0; bottom: 0; height: 20%;
    background: linear-gradient(180deg, var(--carton-blue) 0%, var(--mist) 45%, var(--snow) 80%);
  }

  /* front */
  .front .brand { position: absolute; top: 23%; width: 100%; text-align: center; }
  .brand-name { font-weight: 600; font-size: 5em; line-height: 1; color: var(--ice); letter-spacing: .01em; text-transform: none; }
  .brand-line { font-family: var(--body); font-size: .62em; letter-spacing: .12em; color: var(--mist); margin-top: .7em; }
  .front .claim { position: absolute; top: 47%; width: 100%; text-align: center; font-weight: 600; font-size: 1.8em; line-height: 1.2; color: var(--ice); }
  .front .rule { position: absolute; top: 59%; left: 24%; right: 24%; border-top: 1px solid var(--mist); }
  .front .sub-claim { position: absolute; top: 63.5%; width: 100%; text-align: center; font-weight: 600; font-size: 1em; line-height: 1.3; color: var(--ice); }
  .volume-drop { position: absolute; left: 11%; bottom: 3%; width: 21%; }

  .front-hero { position: absolute; top: 1340px; left: 330px; width: 540px; height: 1560px; font-size: 21.2px; }
  .front-hero .panel-fold { height: 6%; }

  /* info side */
  .benefits { position: absolute; top: 9%; left: 12%; right: 12%; list-style: none; display: flex; flex-direction: column; gap: 34px; }
  .benefit { display: flex; flex-direction: column; align-items: center; gap: 8px; text-align: center; font-size: 1em; line-height: 1.35; color: var(--ice); }
  .benefit-icon { width: 26px; height: 26px; }

  /* back */
  .cert-grid { position: absolute; top: 8%; left: 12%; right: 12%; display: grid; grid-template-columns: 1fr 1fr; }
  .cert-cell { height: 94px; display: flex; align-items: center; justify-content: center; }
  .cert-cell:nth-child(1) { border-right: 1px solid var(--mist); border-bottom: 1px solid var(--mist); }
  .cert-cell:nth-child(2) { border-bottom: 1px solid var(--mist); }
  .cert-cell:nth-child(3) { border-right: 1px solid var(--mist); }
  .cert-badge { width: 70px; height: 70px; border-radius: 50%; border: 2px solid var(--ice); }
  .good-thing { position: absolute; top: 33%; left: 10%; right: 10%; text-align: center; }
  .good-thing h2 { font-weight: 600; font-size: 1.3em; margin-bottom: 10px; }
  .good-thing p { font-family: var(--body); font-size: .78em; line-height: 1.5; color: var(--ice); }
  .contact { position: absolute; top: 60%; width: 100%; text-align: center; font-weight: 500; font-size: 1.05em; line-height: 1.45; }

  /* facts side */
  .facts { position: absolute; top: 8%; left: 11%; right: 11%; }
  .facts h2 { font-weight: 600; font-size: 1.2em; margin-bottom: 8px; }
  .facts table { width: 100%; border-collapse: collapse; font-size: .95em; margin-bottom: 26px; }
  .facts td { padding: 2px 0; border-bottom: 1px solid rgba(255,255,255,.55); }
  .facts td:last-child { text-align: right; }
  .recycle-note { border: 1px solid var(--ice); padding: 14px 10px; text-align: center; font-size: .85em; line-height: 1.45; }
  .recycle-note p + p { margin-top: 12px; }
</style>
</head>
<body>

<svg width="0" height="0" style="position:absolute" aria-hidden="true">
  <symbol id="drop" viewBox="0 0 100 140">
    <path d="M50 4 C62 30 95 62 95 92 A45 45 0 0 1 5 92 C5 62 38 30 50 4 Z" fill="#2aaedf" stroke="#ffffff" stroke-width="5"/>
    <text x="50" y="92" text-anchor="middle" font-family="Oswald, sans-serif" font-weight="600" font-size="24" fill="#ffffff">500</text>
    <text x="50" y="122" text-anchor="middle" font-family="Oswald, sans-serif" font-weight="600" font-size="30" fill="#ffffff">ML</text>
  </symbol>
  <symbol id="ring" viewBox="0 0 26 26">
    <circle cx="13" cy="13" r="11" fill="none" stroke="#ffffff" stroke-width="1.5"/>
  </symbol>
</svg>

<section class="panel-row">
  <article class="panel front">
    <div class="panel-fold"></div>
    <div class="brand"><div class="brand-name">Brindle</div><div class="brand-line">Beverages | Est circa 1860</div></div>
    <div class="claim">100%<br>Spring water</div>
    <div class="rule"></div>
    <div class="sub-claim">Sustainably sourced water<br>in a plant-based<br>carton</div>
    <div class="peaks" role="img" aria-label="Snowy mountain range illustration"></div>
    <svg class="volume-drop" viewBox="0 0 100 140"><use href="#drop"/></svg>
  </article>

  <article class="panel info-side">
    <div class="panel-fold"></div>
    <ul class="benefits">
      <li class="benefit"><svg class="benefit-icon"><use href="#ring"/></svg>Pure water in its simplest form</li>
      <li class="benefit"><svg class="benefit-icon"><use href="#ring"/></svg>100% spring water in a carton that's kind</li>
      <li class="benefit"><svg class="benefit-icon"><use href="#ring"/></svg>It's made from 74% paper</li>
      <li class="benefit"><svg class="benefit-icon"><use href="#ring"/></svg>Totalling 79% renewable content</li>
      <li class="benefit"><svg class="benefit-icon"><use href="#ring"/></svg>All that and it's still recyclable</li>
      <li class="benefit"><svg class="benefit-icon"><use href="#ring"/></svg>Less plastic in the world and a smaller carbon footprint</li>
    </ul>
    <div class="peaks" role="img" aria-label="Snowy mountain range illustration"></div>
  </article>

  <article class="panel back">
    <div class="panel-fold"></div>
    <div class="cert-grid">
      <div class="cert-cell"><div class="cert-badge"></div></div>
      <div class="cert-cell"><div class="cert-badge"></div></div>
      <div class="cert-cell"><div class="cert-badge"></div></div>
      <div class="cert-cell"><div class="cert-badge"></div></div>
    </div>
    <div class="good-thing">
      <h2>You just did a good thing</h2>
      <p>This carton is made mainly from plants, which pull CO2 from the air as they grow. Cartons are lighter to ship and easy to recycle. It's not perfect, but it's a better option, and every carton you choose helps the planet.</p>
    </div>
    <div class="contact">Website &amp; social<br>brindlewater.com.au<br>Chirp: @brindle<br>Snapgram: @brindlewater</div>
    <div class="peaks" role="img" aria-label="Snowy mountain range illustration"></div>
  </article>

  <article class="panel facts-side">
    <div class="panel-fold"></div>
    <div class="facts">
      <h2>Typical water analysis (mg/L)</h2>
      <table>
        <tr><td>Calcium</td><td>10</td></tr>
        <tr><td>Magnesium</td><td>2.5</td></tr>
        <tr><td>Potassium</td><td>1</td></tr>
        <tr><td>Sodium</td><td>9</td></tr>
        <tr><td>Chloride</td><td>11</td></tr>
        <tr><td>Oxidised nitrogen</td><td>0.6</td></tr>
        <tr><td>Silica</td><td>16</td></tr>
        <tr><td>Bicarbonate</td><td>160</td></tr>
      </table>
      <h2>Packaging facts</h2>
      <table>
        <tr><td>Paper</td><td>66%</td></tr>
        <tr><td>Plant-based plastic</td><td>5%</td></tr>
        <tr><td>PE plastic</td><td>4%</td></tr>
        <tr><td>Foil</td><td>5%</td></tr>
      </table>
      <div class="recycle-note">
        <p>Please close the lid and recycle.<br>Do not crush or flatten.</p>
        <p>Proud to bring you pure spring water</p>
      </div>
    </div>
    <div class="peaks" role="img" aria-label="Snowy mountain range illustration"></div>
  </article>
</section>

<article class="panel front front-hero">
  <div class="panel-fold"></div>
  <div class="brand"><div class="brand-name">Brindle</div><div class="brand-line">Beverages | Est circa 1860</div></div>
  <div class="claim">100%<br>Spring water</div>
  <div class="rule"></div>
  <div class="sub-claim">Sustainably sourced water<br>in a plant-based<br>carton</div>
  <div class="peaks" role="img" aria-label="Snowy mountain range illustration"></div>
  <svg class="volume-drop" viewBox="0 0 100 140"><use href="#drop"/></svg>
</article>

</body>
</html>
```